Design webpages + logo for a new social media consultancy company called = "Tallow Creek Mosaic"

I am in need of a graphic visualisation of what we do

page 1
HOW MUCH DID YOU MAKE FROM SOCIAL MEDIA LAST YEAR?
if you don't know the direct answer to this you should talk to us

page 2
WHAT DO WE DO
we commercialise your social media efforts
we calculate your social media ROI
we improve your efficiencies
we will map you target consumer and help you use that data to target them better

page 3
HOW DO WE DO IT
We offer to come in and asses your current social media activities, based on that we can build a matrix around your set up that will allow you to not to only make you money from your social media efforts, but also measure your spend versus you income to asses your efficiency.
In short we will help you to run your social media marketing as a commercial sales department.

page 4
UP YOUR GAME AND LET US HELP YOU MEASURE YOUR ROI ON SOCIAL MEDIA
contact page with links to social media, facebook, instagram and linkedin

Target Market(s)

companies who need strategic social media support

Logo Text

Tallow Creek Mosaic

Number of Pages Required

4 page

Colors

Designer to choose colors to be used in the design.

Requirements
Must have
• visuals that show
• - social media
• - visualize ROI = return on investment
• - how to do marketing without losing money
Nice to have
• motion graphic style to explain the service offered
Should not have
• real pictures (of people etc)

```html
<!DOCTYPE html>
<html lang="en">
<head>
<meta charset="UTF-8">
<title>Tallow Creek Mosaic – What We Do</title>
<link rel="stylesheet" href="https://fonts.googleapis.com/css2?family=Arimo:wght@700&family=Roboto:wght@400&display=swap">
<style>
  :root {
    --bg-start: #1e5cc6;
    --bg-end: #0aa2e6;
    --text: #ffffff;
    --button: #0b82fb;
    --arrow: #1f63c9;
    --art-orange: #f3a11a;
    --art-light: #dfeefc;
    --art-blue: #2d6fd2;
  }
  * { margin: 0; padding: 0; box-sizing: border-box; }
  html, body { width: 1200px; height: 543px; overflow: hidden; }
  body { background: var(--bg-start); }
  .what-we-do {
    position: relative;
    width: 1200px;
    height: 543px;
    overflow: hidden;
    background: linear-gradient(110deg, var(--bg-start) 0%, #1870d4 45%, var(--bg-end) 100%);
    color: var(--text);
  }
  .section-title {
    position: absolute;
    left: 89px;
    top: 112px;
    font-family: "Arimo", Arial, sans-serif;
    font-weight: 700;
    font-size: 32px;
    letter-spacing: 0.2px;
  }
  .service-list {
    position: absolute;
    left: 88px;
    top: 169px;
    width: 470px;
    list-style: none;
    font-family: "Roboto", Arial, sans-serif;
    font-size: 18px;
    line-height: 24px;
  }
  .service-list li {
    position: relative;
    padding-left: 28px;
    margin-bottom: 24px;
  }
  .service-icon {
    position: absolute;
    left: 0;
    top: 5px;
    width: 13px;
    height: 13px;
  }
  .cta-button {
    position: absolute;
    left: 93px;
    top: 392px;
    width: 175px;
    height: 53px;
    border-radius: 27px;
    background: var(--button);
    color: var(--text);
    font-family: "Arimo", Arial, sans-serif;
    font-weight: 700;
    font-size: 16px;
    text-decoration: none;
    display: flex;
    align-items: center;
    justify-content: center;
  }
  .service-illustration {
    position: absolute;
    left: 535px;
    top: 24px;
    width: 592px;
    height: 490px;
    border-radius: 40px;
    background:
      radial-gradient(ellipse at 45% 40%, var(--art-orange) 0%, rgba(243,161,26,0.6) 25%, transparent 50%),
      radial-gradient(ellipse at 55% 60%, var(--art-light) 0%, transparent 55%),
      linear-gradient(160deg, rgba(45,111,210,0.35), rgba(45,111,210,0.15));
  }
</style>
</head>
<body>
  <main class="what-we-do">
    <h1 class="section-title">WHAT WE DO</h1>
    <ul class="service-list">
      <li>
        <svg class="service-icon" viewBox="0 0 14 14" aria-hidden="true"><circle cx="7" cy="7" r="7" fill="#fff"/><path d="M4 7h5M7 4.5 9.5 7 7 9.5" stroke="var(--arrow)" stroke-width="1.6" fill="none" stroke-linecap="round" stroke-linejoin="round"/></svg>
        We commercialise your social media efforts
      </li>
      <li>
        <svg class="service-icon" viewBox="0 0 14 14" aria-hidden="true"><circle cx="7" cy="7" r="7" fill="#fff"/><path d="M4 7h5M7 4.5 9.5 7 7 9.5" stroke="var(--arrow)" stroke-width="1.6" fill="none" stroke-linecap="round" stroke-linejoin="round"/></svg>
        We calculate your social media ROI
      </li>
      <li>
        <svg class="service-icon" viewBox="0 0 14 14" aria-hidden="true"><circle cx="7" cy="7" r="7" fill="#fff"/><path d="M4 7h5M7 4.5 9.5 7 7 9.5" stroke="var(--arrow)" stroke-width="1.6" fill="none" stroke-linecap="round" stroke-linejoin="round"/></svg>
        We improve your efficiencies
      </li>
      <li>
        <svg class="service-icon" viewBox="0 0 14 14" aria-hidden="true"><circle cx="7" cy="7" r="7" fill="#fff"/><path d="M4 7h5M7 4.5 9.5 7 7 9.5" stroke="var(--arrow)" stroke-width="1.6" fill="none" stroke-linecap="round" stroke-linejoin="round"/></svg>
        We will map you target consumer and help you use that data to target them better
      </li>
    </ul>
    <a class="cta-button" href="#">CLICK HERE</a>
    <div class="service-illustration" role="img" aria-label="Isometric illustration of a laptop and phone with money, coins, a payment card, currency icons, clouds and people handling online payments"></div>
  </main>
</body>
</html>
```